Transform Your Giving

I need a tri-fold brochure that will fit in a standard number 10 business envelope. Meadowlark and Allied Services is a charitable nonprofit. The goal of this brochure is to stimulate people into thinking about other ways to make a donation. The design should communicate the essential information on donation options, create a sense of professional integrity, be graphically sharp, easy to read and laid out in a way that doesn't make the material appear crowded.

```html
<!DOCTYPE html>
<html lang="en">
<head>
<meta charset="utf-8">
<title>Transform Your Giving – Tri-fold Brochure</title>
<link rel="stylesheet" href="https://fonts.googleapis.com/css2?family=Bebas+Neue&family=Montserrat:ital,wght@0,400;0,500;0,600;0,700;1,500;1,600;1,700&display=swap">
<style>
:root{
  --purple:#2d2a73;
  --purple-deep:#231f5e;
  --purple-light:#4b3f9a;
  --green:#3fae49;
  --green-dark:#2f9a3a;
  --ink:#1d1d2b;
  --paper:#ffffff;
  --backdrop:#ffffff;
}
*{box-sizing:border-box;margin:0;padding:0}
html,body{width:720px;height:1200px;overflow:hidden;background:var(--backdrop)}
body{font-family:"Montserrat",sans-serif;color:var(--ink)}
.stage{position:absolute;left:2px;top:0;width:1484px;height:2492px;transform:scale(0.4815);transform-origin:0 0}
.sheet{position:absolute;left:120px;width:1250px;height:966px;background:var(--paper);box-shadow:0 2px 8px rgba(0,0,0,.18);overflow:hidden}
.sheet--outside{top:207px}
.sheet--inside{top:1248px}
.panel{position:absolute;top:0;height:966px;overflow:hidden}
.p1{left:0;width:415px}.p2{left:415px;width:418px}.p3{left:833px;width:417px}
.abs{position:absolute}
.photo{position:absolute}
.body-text{font-size:12.6px;line-height:15.2px;font-weight:500}
.pill{display:inline-block;background:var(--green);color:#fff;font-weight:700;font-size:15px;letter-spacing:.5px;padding:4px 9px;border-radius:0 12px 12px 0}
.tick-list{list-style:none}
.tick-list li{display:flex;align-items:flex-start;gap:8px;font-size:12.6px;font-weight:600}
.tick{flex:none;width:10px;height:10px;border:1.4px solid var(--purple);margin-top:2px;position:relative}
.tick::after{content:"";position:absolute;left:2px;top:0;width:3px;height:5px;border:solid var(--purple);border-width:0 1.4px 1.4px 0;transform:rotate(40deg)}
.brand-name{font-family:"Montserrat",sans-serif;font-weight:700;color:var(--purple);letter-spacing:1px}
.option-head{display:flex;gap:14px;align-items:flex-start}
.option-title{font-size:16.5px;font-weight:700;color:var(--purple);line-height:19px}
.option-sub{font-size:12.6px;font-weight:700;font-style:italic;color:var(--purple);line-height:15px}
.bubble{position:absolute;width:100px;height:100px;border-radius:50%;background:radial-gradient(circle at 40% 35%,rgba(255,255,255,.7),rgba(200,200,230,.45));border:2px solid rgba(255,255,255,.7);display:flex;flex-direction:column;align-items:center;justify-content:center;gap:4px;font-size:12.5px;font-weight:700;color:var(--purple);text-align:center;line-height:13px}
</style>
</head>
<body>
<div class="stage">

  <!-- OUTSIDE SHEET -->
  <section class="sheet sheet--outside">
    <!-- Panel: impact -->
    <div class="panel p1">
      <div class="photo" role="img" aria-label="Photo of a smiling older woman in glasses reading a book outdoors" style="left:0;top:0;width:415px;height:620px;background:linear-gradient(160deg,#b9a65a 0%,#d9c7a4 40%,#e9b9b5 65%,#8c9a6a 100%)"></div>
      <svg class="abs" style="left:0;top:520px" width="415" height="170" viewBox="0 0 415 170">
        <path d="M0 90 Q140 0 415 150 L415 170 L0 170Z" fill="var(--green)"/>
        <path d="M0 112 Q140 25 415 182 L415 200 L0 200Z" fill="#fff"/>
      </svg>
      <div class="abs" style="left:0;top:641px;width:288px;height:42px;background:var(--purple);border-radius:0 22px 22px 0;color:#fff;font-family:'Bebas Neue',sans-serif;font-size:34px;line-height:44px;padding-left:28px">THE IMPACT OF YOUR GIFT</div>
      <p class="abs body-text" style="left:29px;top:708px;width:360px">Your generosity drives our mission. With every Smart gift you're supporting Meadowlark and Allied Services. Join our community of Smart Givers today and make an enduring impact. With Smart Giving your generosity reaches further. Begin your Smart Giving journey with us today.</p>
      <ul class="abs tick-list" style="left:29px;top:817px;display:grid;row-gap:12px">
        <li><span class="tick"></span>Stocks and Securities</li>
        <li><span class="tick"></span>DAFs</li>
        <li><span class="tick"></span>QCDs</li>
        <li><span class="tick"></span>Crypto</li>
        <li><span class="tick"></span>Charitable Annuity</li>
      </ul>
    </div>

    <!-- Panel: contact -->
    <div class="panel p2" style="background:linear-gradient(90deg,var(--purple-deep) 0%,var(--purple-light) 60%,var(--purple-deep) 100%);color:#fff;text-align:center">
      <p class="abs" style="left:28px;top:30px;width:362px;font-size:12.2px;line-height:15.2px;font-weight:500">To learn more about Smart Giving Options and how they can benefit you and Meadowlark and Allied Services, please reach out to our team. We're here to help you navigate these giving methods and answer any question you may have.</p>
      <div class="abs" style="left:30px;top:135px;width:360px;height:123px;background:#fff;border-radius:24px;text-align:left;color:var(--purple)">
        <svg class="abs" style="left:10px;top:8px" width="340" height="110" viewBox="0 0 340 110">
          <text x="2" y="36" font-family="Montserrat" font-weight="700" font-size="44" fill="var(--green)">“</text>
          <path d="M62 22 H335 Q340 22 340 30 V85 Q340 95 330 95 H212" fill="none" stroke="var(--green)" stroke-width="1.3"/>
          <text x="150" y="118" font-family="Montserrat" font-weight="700" font-size="44" fill="var(--green)">”</text>
        </svg>
        <p class="abs" style="left:12px;top:46px;width:320px;font-size:15px;line-height:19px;font-style:italic;font-weight:500">Being kind to others is a way of being good to yourself.<br><b style="font-weight:700">- Helen Ashgrove</b></p>
      </div>
      <div class="abs" style="left:0;top:300px;width:418px">
        <div class="brand-name" style="color:#fff;font-size:30px">Meadowlark</div>
        <div style="font-size:7.5px;font-weight:700;letter-spacing:.5px;margin-top:3px">MEADOWLARK AND ALLIED SERVICES, INC.</div>
      </div>
      <div class="abs" style="left:57px;top:402px;width:305px;height:58px;background:var(--green);border-radius:14px;font-size:12.2px;line-height:15px;font-weight:500;padding-top:6px">If you do not have a will, go to<br><b>www.SimpleWillNow.org</b><br>In 20 minutes you can have a legal will for free.</div>
      <div class="abs" style="left:0;top:515px;width:418px;font-size:15px;font-weight:700;text-decoration:underline">CONTACT US</div>
      <p class="abs" style="left:0;top:548px;width:418px;font-size:12.2px;line-height:15px;font-weight:500">Have more question?<br>Please contact us at Meadowlark &amp; Allied Services</p>
      <svg class="abs" style="left:200px;top:587px" width="18" height="170" viewBox="0 0 18 170">
        <circle cx="9" cy="9" r="9" fill="var(--green)"/><path d="M9 4a3.2 3.2 0 0 0-3.2 3.2c0 2.4 3.2 6 3.2 6s3.2-3.6 3.2-6A3.2 3.2 0 0 0 9 4z" fill="#fff"/>
        <circle cx="9" cy="67" r="9" fill="var(--green)"/><path d="M6 62l2 0 1 3-1.2 1a6 6 0 0 0 2.5 2.5l1-1.2 3 1v2c-5 .5-9-3.5-8.5-8.3z" fill="#fff"/>
        <circle cx="9" cy="113" r="9" fill="var(--green)"/><rect x="4.5" y="109.5" width="9" height="7" fill="#fff"/><path d="M4.5 109.5l4.5 4 4.5-4" fill="none" stroke="var(--green)" stroke-width="1"/>
        <circle cx="9" cy="160" r="9" fill="var(--green)"/><circle cx="9" cy="160" r="4.8" fill="none" stroke="#fff" stroke-width="1.2"/><path d="M4.2 160h9.6M9 155.2v9.6" stroke="#fff" stroke-width="1"/>
      </svg>
      <p class="abs" style="left:0;top:608px;width:418px;font-size:12.2px;line-height:15.5px;font-weight:500">1420 Prairie Ridge Rd.<br>Suite 2, Fargo, ND &nbsp;58102</p>
      <p class="abs" style="left:0;top:668px;width:418px;font-size:12.2px;font-weight:500">555-014-2200 (ext. 100)</p>
      <p class="abs" style="left:0;top:714px;width:418px;font-size:12.2px;font-weight:500">info@meadowlarkallied.org</p>
      <p class="abs" style="left:0;top:760px;width:418px;font-size:12.2px;font-weight:500">www.meadowlarkallied.org</p>
      <div class="abs" style="left:0;top:817px;width:418px;font-size:15px;font-weight:700;text-decoration:underline">Follow us:</div>
      <svg class="abs" style="left:148px;top:843px" width="124" height="22" viewBox="0 0 124 22">
        <path d="M20 11H52M72 11H102" stroke="var(--green)" stroke-width="1.5"/>
        <circle cx="11" cy="11" r="10" fill="var(--green)"/><circle cx="62" cy="11" r="10" fill="var(--green)"/><circle cx="112" cy="11" r="10" fill="var(--green)"/>
      </svg>
      <p class="abs" style="left:38px;top:898px;width:342px;font-size:7.6px;line-height:9.4px">This material is for general information only and is not tax, legal or accounting advice. Meadowlark and Allied Services is not a fiduciary. Please consult your own tax or financial advisor before choosing a giving method.</p>
    </div>

    <!-- Panel: cover -->
    <div class="panel p3">
      <h1 class="abs" style="left:0;top:24px;width:417px;text-align:center;font-family:'Bebas Neue',sans-serif;font-weight:400;font-size:52px;line-height:52px;color:var(--green)">TRANSFORM YOUR GIVING</h1>
      <div class="abs" style="left:42px;top:77px;width:334px;height:30px;background:var(--purple);border-radius:16px;color:#fff;text-align:center;font-weight:700;font-size:22px;line-height:30px;letter-spacing:.5px">BE STRATEGIC, BE SMART</div>
      <p class="abs" style="left:0;top:116px;width:417px;text-align:center;font-size:16.5px;line-height:20.5px;color:#333">Discover the impact of Smart Giving with<br>Meadowlark and Allied Services</p>
      <div class="photo" role="img" aria-label="Photo of a laughing senior couple walking arm in arm through an autumn park" style="left:0;top:165px;width:417px;height:700px;background:linear-gradient(135deg,#9a8d55 0%,#c7a978 35%,#7f8fc2 60%,#6e6a45 100%)"></div>
      <svg class="abs" style="left:0;top:160px" width="417" height="90" viewBox="0 0 417 90">
        <path d="M0 0H417V30Q300 90 170 70 Q80 55 0 15Z" fill="#fff"/>
        <path d="M40 20 Q200 110 417 15 V30 Q240 95 40 20Z" fill="var(--green)"/>
      </svg>
      <svg class="abs" style="left:0;top:780px" width="417" height="186" viewBox="0 0 417 186">
        <path d="M0 80 Q170 -15 417 60 V186 H0Z" fill="var(--purple)"/>
        <path d="M0 100 Q190 5 417 90 V186 H0Z" fill="#fff"/>
      </svg>
      <div class="bubble" style="left:28px;top:218px"><svg width="60" height="46" viewBox="0 0 60 46"><circle cx="18" cy="14" r="12" fill="none" stroke="var(--purple)" stroke-width="2.5"/><circle cx="42" cy="14" r="12" fill="none" stroke="var(--purple)" stroke-width="2.5"/><circle cx="30" cy="32" r="12" fill="none" stroke="var(--purple)" stroke-width="2.5"/></svg>Crypto</div>
      <div class="bubble" style="left:285px;top:275px"><svg width="56" height="46" viewBox="0 0 56 46"><circle cx="20" cy="18" r="13" fill="none" stroke="var(--purple)" stroke-width="2.5" stroke-dasharray="4 2"/><circle cx="38" cy="30" r="13" fill="none" stroke="var(--purple)" stroke-width="2.5" stroke-dasharray="4 2"/></svg>DAF's</div>
      <div class="bubble" style="left:28px;top:478px"><svg width="50" height="42" viewBox="0 0 50 42"><path d="M3 3V39H48" fill="none" stroke="var(--purple)" stroke-width="3"/><rect x="10" y="22" width="6" height="14" fill="var(--purple)"/><rect x="20" y="14" width="6" height="22" fill="var(--purple)"/><rect x="30" y="18" width="6" height="18" fill="var(--purple)"/><rect x="40" y="10" width="6" height="26" fill="var(--purple)"/></svg>Stocks &amp;<br>Securities</div>
      <div class="bubble" style="left:285px;top:538px"><svg width="46" height="48" viewBox="0 0 46 48"><rect x="3" y="14" width="40" height="9" fill="var(--purple)"/><rect x="6" y="25" width="34" height="21" fill="var(--purple)"/><rect x="21" y="12" width="4" height="34" fill="#dcdcef"/><path d="M23 13C14 2 8 8 14 13M23 13C32 2 38 8 32 13" fill="none" stroke="var(--purple)" stroke-width="2.5"/></svg>QCDs</div>
      <div class="bubble" style="left:28px;top:705px"><svg width="52" height="44" viewBox="0 0 52 44"><ellipse cx="14" cy="38" rx="10" ry="3.5" fill="var(--purple)"/><ellipse cx="14" cy="31" rx="10" ry="3.5" fill="var(--purple)"/><ellipse cx="32" cy="38" rx="10" ry="3.5" fill="var(--purple)"/><ellipse cx="32" cy="31" rx="10" ry="3.5" fill="var(--purple)"/><ellipse cx="32" cy="24" rx="10" ry="3.5" fill="var(--purple)"/><circle cx="40" cy="8" r="6" fill="var(--purple)"/></svg>Charitable<br>Annuity</div>
      <div class="abs" style="left:0;top:870px;width:417px;text-align:center">
        <div class="brand-name" style="font-size:40px">Meadowlark</div>
        <div style="font-size:10px;font-weight:700;color:var(--purple);margin-top:2px">MEADOWLARK AND ALLIED SERVICES, INC.</div>
      </div>
    </div>
  </section>

  <!-- INSIDE SHEET -->
  <section class="sheet sheet--inside">
    <div class="panel p1">
      <p class="abs body-text" style="left:29px;top:28px;width:360px">We would like to introduce you to five Strategic and Smart ways to give that could potentially be more beneficial to you compared to traditional cash donations. We encourage you to keep this information as a guide for your future contributions.</p>
      <div class="abs option-head" style="left:29px;top:122px;width:370px">
        <svg width="72" height="62" viewBox="0 0 72 62" style="flex:none;margin-top:8px"><path d="M3 2V58H70" fill="none" stroke="var(--green)" stroke-width="4"/><rect x="14" y="32" width="7" height="22" fill="var(--green)"/><rect x="27" y="24" width="7" height="30" fill="var(--green)"/><rect x="40" y="30" width="7" height="24" fill="var(--green)"/><rect x="53" y="22" width="7" height="32" fill="var(--green)"/><path d="M12 22L26 10L40 18L64 4" fill="none" stroke="var(--green)" stroke-width="3"/></svg>
        <div><div class="option-title">Gifts of Stocks or Appreciated Assets Strategic &amp; Smart</div><div class="option-sub">Consider your long-term publicly traded stock as a way to give to your favorite charity.</div></div>
      </div>
      <p class="abs body-text" style="left:29px;top:217px;width:360px">You can make a significantly bigger impact when you donate long-term appreciated securities, including stock, mutual funds, and bonds, directly to your favorite charity.</p>
      <span class="abs pill" style="left:29px;top:286px">HOW DOES IT WORK?</span>
      <p class="abs body-text" style="left:29px;top:336px;width:360px">When you donate stock to a charity, you will generally take a tax deduction for the full market value. Because you are donating stock, your contribution and tax deduction may be significantly higher than contributing the after-tax proceeds. The same benefits apply when you donate mutual funds or bonds.</p>
      <div class="abs option-head" style="left:29px;top:466px;width:370px">
        <svg width="72" height="72" viewBox="0 0 72 72" style="flex:none;margin-top:6px"><circle cx="24" cy="26" r="16" fill="none" stroke="var(--green)" stroke-width="3" stroke-dasharray="5 2.5"/><circle cx="24" cy="26" r="7" fill="none" stroke="var(--green)" stroke-width="2.5"/><circle cx="48" cy="48" r="16" fill="none" stroke="var(--green)" stroke-width="3" stroke-dasharray="5 2.5"/><circle cx="48" cy="48" r="7" fill="none" stroke="var(--green)" stroke-width="2.5"/></svg>
        <div><div class="option-title">Donor-Advised Fund (DAF)<br>Strategic &amp; Smart</div><div class="option-sub">Consider a DAF – a simple, flexible, and tax-advantageous way to give to your favorite charities.</div></div>
      </div>
      <p class="abs body-text" style="left:29px;top:566px;width:360px">A Donor-Advised Fund (DAF), is like a charitable investment account for the sole purpose of supporting your favorite charities.</p>
      <span class="abs pill" style="left:29px;top:631px">HOW DOES IT WORK?</span>
      <p class="abs body-text" style="left:29px;top:681px;width:360px">You establish a DAF and contribute cash, stocks, or non-publicly traded assets, cryptocurrency, and private company stock to be eligible for an immediate tax deduction. Those funds are contributed for tax-free growth. You can recommend grants be made from your DAF to any IRS qualified public charity.</p>
      <div class="photo" role="img" aria-label="Photo of a happy older couple lying on the grass in a park" style="left:0;top:826px;width:415px;height:140px;background:linear-gradient(100deg,#6f9a3a 0%,#a7b66a 45%,#5f8a32 100%)"></div>
      <svg class="abs" style="left:0;top:785px" width="415" height="181" viewBox="0 0 415 181">
        <path d="M0 0H415V181 Q320 40 0 40Z" fill="#fff"/>
        <path d="M0 40 Q320 20 415 181 L395 181 Q300 45 0 55Z" fill="var(--purple)"/>
      </svg>
    </div>

    <div class="panel p2">
      <div class="photo" role="img" aria-label="Photo of a senior couple at home looking at a tablet together" style="left:0;top:0;width:418px;height:525px;background:linear-gradient(180deg,#f3f4f6 0%,#d9d4cf 45%,#8a8a96 75%,#ffffff 100%)"></div>
      <div class="abs option-head" style="left:28px;top:530px;width:375px">
        <svg width="62" height="76" viewBox="0 0 62 76" style="flex:none;margin-top:4px"><rect x="2" y="22" width="58" height="14" fill="var(--green)"/><rect x="6" y="39" width="50" height="35" fill="var(--green)"/><rect x="28" y="20" width="6" height="54" fill="#fff"/><path d="M31 21C18 2 8 10 18 21M31 21C44 2 54 10 44 21" fill="none" stroke="var(--green)" stroke-width="4"/></svg>
        <div><div class="option-title">Qualified Charitable Distributions (QCDs) Strategic &amp; Smart</div><div class="option-sub">Consider a QCD – when planning your IRA withdrawal strategy...and donate to your favorite charity.</div></div>
      </div>
      <p class="abs body-text" style="left:28px;top:637px;width:362px">IRA owners at age 70 or over can transfer dollars from their IRA to charity tax-free each year. These transfers known as Qualified Charitable Distributions (QCDs) offer eligible older Americans a great way to easily give to charity.</p>
      <span class="abs pill" style="left:28px;top:736px">HOW DOES IT WORK?</span>
      <p class="abs body-text" style="left:28px;top:783px;width:362px">Are you 72 and required to take a minimum distribution (RMD) from your IRA but do not need the funds? Consider a Qualified Charitable Distribution. Normally, distributions from a traditional IRA are taxable when received. With a QCD, these distributions become tax-free when paid directly from the IRA to your favorite eligible charity. An IRA owner wishing to make a QCD should contact their IRA trustee, allowing time to complete the transaction before the end of the year to receive the tax benefit.</p>
    </div>

    <div class="panel p3">
      <div class="abs option-head" style="left:32px;top:28px;width:370px">
        <svg width="62" height="54" viewBox="0 0 62 54" style="flex:none"><circle cx="16" cy="16" r="13" fill="none" stroke="var(--green)" stroke-width="3"/><circle cx="46" cy="16" r="13" fill="none" stroke="var(--green)" stroke-width="3"/><circle cx="31" cy="38" r="13" fill="none" stroke="var(--green)" stroke-width="3"/><path d="M31 29L25 38L31 47L37 38Z" fill="var(--green)"/></svg>
        <div><div class="option-title">Cryptocurrency Strategic &amp; Smart</div><div class="option-sub">Consider donating Bitcoin and other cryptocurrencies to your favorite charity.</div></div>
      </div>
      <p class="abs body-text" style="left:30px;top:103px;width:360px">Bitcoin and other cryptocurrencies can be donated to charity just like other appreciated assets such as stocks and other business interests. Before you sell bitcoin and donate the after-tax proceeds, consider donating your bitcoin directly to a favorite charity.</p>
      <span class="abs pill" style="left:28px;top:200px">HOW DOES IT WORK?</span>
      <p class="abs body-text" style="left:30px;top:241px;width:360px">Many donors find it useful to open a Donor-Advised Fund (DAF). This strategy includes two significant benefits, both for you and your favorite charity.</p>
      <ul class="abs tick-list" style="left:30px;top:307px;width:362px;display:grid;row-gap:14px">
        <li style="font-weight:500"><span class="tick"></span><span class="body-text">Your tax deduction will be equal to the fair market value of the donated bitcoin (as determined by a qualified appraisal).</span></li>
        <li style="font-weight:500"><span class="tick"></span><span class="body-text">Your cryptocurrency donation is tax-smart because it may eliminate capital gains taxes on the value /appreciation AND your favorite charity will receive &nbsp;100% of the value of the contribution.</span></li>
      </ul>
      <p class="abs body-text" style="left:30px;top:446px;width:360px">Often charities are not able to accept direct donations of bitcoin/crypto so using a DAF is a great way to donate these assets.</p>
      <div class="abs option-head" style="left:30px;top:523px;width:370px">
        <svg width="62" height="64" viewBox="0 0 62 64" style="flex:none;margin-top:4px"><path d="M2 8H20M2 14H14" stroke="var(--green)" stroke-width="2.5"/><circle cx="46" cy="12" r="9" fill="var(--green)"/><ellipse cx="16" cy="58" rx="13" ry="4.5" fill="var(--green)"/><ellipse cx="16" cy="49" rx="13" ry="4.5" fill="var(--green)"/><ellipse cx="40" cy="58" rx="13" ry="4.5" fill="var(--green)"/><ellipse cx="40" cy="49" rx="13" ry="4.5" fill="var(--green)"/><ellipse cx="40" cy="40" rx="13" ry="4.5" fill="var(--green)"/><path d="M8 36Q18 22 34 26" fill="none" stroke="var(--green)" stroke-width="2" stroke-dasharray="3 3"/></svg>
        <div><div class="option-title">Charitable Gift Annuity<br>Strategic &amp; Smart</div><div class="option-sub">Consider establishing a Charitable Gift Annuity</div></div>
      </div>
      <p class="abs body-text" style="left:30px;top:608px;width:360px">You make a donation to a single charity. The gift is set aside in a reserve account and invested.</p>
      <span class="abs pill" style="left:28px;top:654px">HOW DOES IT WORK?</span>
      <p class="abs body-text" style="left:30px;top:697px;width:362px">A charitable gift annuity is a contract between a donor and a charity. As a donor, you make a sizable gift to charity using cash, securities, or possibly other assets. This money is then invested. &nbsp;In return, you become eligible to take a partial tax deduction for your donation, plus you receive a fixed stream of income from the charity for the rest of your life. At the end of your life (as well as your spouse's, if you're giving as a couple), the charity receives the remainder of the gift.</p>
      <svg class="abs" style="left:0;top:846px" width="417" height="120" viewBox="0 0 417 120">
        <path d="M0 120 Q150 15 417 0 V120Z" fill="var(--purple)"/>
        <path d="M0 120 Q150 30 417 16 V0 Q150 10 0 116Z" fill="#fff"/>
      </svg>
      <div class="abs" style="left:120px;top:925px;width:270px;text-align:right;color:#fff;font-size:19px;letter-spacing:.3px">www.meadowlarkallied.org</div>
    </div>
  </section>

</div>
</body>
</html>
```